We are a local Communty Pharmacy wishing to promote and market a specialised Pharmaceutical Service

We would like a design that is professional and enticing ( according to the brief In attached files)
We wish to Market Meadowbrook Pharmacy as a specialist side of our business.
We have the expertise a purpose built preparation laboratory.
The main purpose is an Internet presence that entices prospective patients to contact or visit our physical store.

Target Market(s)

Patients Medicos and Veterinary clients

Industry/Entity Type

Pharmacy

Coding

Coded - Design and coding required

Number of Pages Required

1 page

Requirements
Must have
• Clear friendly image
Nice to have
• soft enticing feel
Should not have
• No crass loud unprofessional elements

```html
<!DOCTYPE html>
<html lang="en">
<head>
<meta charset="utf-8">
<title>Meadowbrook Pharmacy</title>
<link href="https://fonts.googleapis.com/css2?family=Open+Sans:wght@400;600&family=Roboto+Slab:wght@400;700&display=swap" rel="stylesheet">
<style>
:root{
  --teal:#4cc3da;
  --teal-dark:#2fa9c2;
  --green:#45d68c;
  --circle-blue:#5bc6ea;
  --circle-green:#6fe0a2;
  --circle-teal:#34d3b2;
  --ink:#333a3f;
  --muted:#7b8389;
  --line:#e3e6e8;
  --white:#ffffff;
  --page:#ffffff;
}
*{box-sizing:border-box;margin:0;padding:0}
html,body{width:748px;height:1200px;overflow:hidden;background:var(--page)}
body{font-family:"Open Sans",Arial,sans-serif;color:var(--ink);position:relative}
.topbar{height:20px;background:var(--teal);color:var(--white);font-size:7.5px;display:flex;align-items:center;justify-content:space-between;padding:0 30px}
.topbar .right span{margin-left:12px}
.header{height:62px;display:flex;align-items:center;justify-content:space-between;padding:0 30px}
.brand{display:flex;align-items:center;gap:7px;font-family:"Roboto Slab",Georgia,serif;font-weight:700;color:var(--teal-dark);font-size:14px;line-height:1.05}
.brand .dot{width:20px;height:20px;border-radius:50%;background:var(--green)}
.nav{display:flex;align-items:center;gap:16px;font-size:8px;font-weight:600;color:var(--ink);letter-spacing:.3px}
.nav svg{margin-left:4px}
.hero{position:relative;height:296px;background:linear-gradient(100deg,#c9ced2 0%,#dcdfe1 14%,#e7c7ad 26%,#f1d6c2 34%,#fbfaf7 46%,#f6efe6 56%,#f3b45e 64%,#f7f7f5 74%,#e5d2c2 84%,#c7cdd2 100%)}
.hero .arrow{position:absolute;top:50%;width:18px;height:18px;margin-top:-9px;border-radius:50%;background:rgba(0,0,0,.25);display:flex;align-items:center;justify-content:center}
.hero .arrow.prev{left:22px}.hero .arrow.next{right:22px}
.about{position:relative;height:242px;padding:26px 0 0 62px}
.about h2{font-family:"Roboto Slab",Georgia,serif;font-size:15px;font-weight:700;color:var(--ink);margin-bottom:12px}
.about p{width:340px;font-size:7.4px;line-height:1.75;color:var(--muted);margin-bottom:8px}
.about .more{font-size:7.6px;color:var(--teal-dark);font-weight:600}
.about .circles{position:absolute;left:456px;top:12px}
.featured{height:270px;padding-top:20px}
.featured h2{text-align:center;font-family:"Roboto Slab",Georgia,serif;font-size:15px;font-weight:700;margin-bottom:20px}
.products{display:flex;gap:9px;margin-left:62px;width:625px}
.product{width:150px;height:145px;border:1px solid var(--line);display:flex;align-items:center;justify-content:center;background:var(--white)}
.product .shot{width:104px;height:92px;border-radius:6px}
.pager{display:flex;justify-content:center;gap:6px;margin-top:24px}
.pager span{width:18px;height:18px;border-radius:50%;background:#b9bfc3;display:flex;align-items:center;justify-content:center}
.callband{position:absolute;top:890px;left:0;width:748px;height:84px;background:var(--green);color:var(--white);text-align:center;padding-top:16px}
.callband .icon{width:20px;height:20px;margin:0 auto 3px;display:block}
.callband .label{font-size:7.5px}
.callband .number{font-family:"Roboto Slab",Georgia,serif;font-size:15px;font-weight:700;letter-spacing:.5px}
.map{position:absolute;top:974px;left:0;width:748px;height:160px;background:linear-gradient(160deg,#b9d2e2 0%,#cfdcc4 18%,#dfe5d2 36%,#e9e7dc 52%,#d6e1c9 68%,#e6e4d8 84%,#c9d8c0 100%)}
.footer{position:absolute;top:1134px;left:0;width:748px;height:66px;background:var(--teal);color:var(--white);display:flex;align-items:center;justify-content:space-between;padding:0 30px}
.footer .links{font-size:7.5px;display:flex;gap:13px;margin-bottom:6px}
.footer .copy{font-size:7px;opacity:.9}
.social{display:flex;gap:6px}
.social span{width:16px;height:16px;background:var(--white);border-radius:2px;opacity:.95}
</style>
</head>
<body>
<div class="topbar">
  <div>Opening Hours: Monday to Saturday - 9am to 5pm</div>
  <div class="right"><span>Call Us Now</span><span>1 800 555 0142</span><span>Login</span><span>Register</span></div>
</div>

<header class="header">
  <div class="brand"><span class="dot"></span><span>Meadowbrook<br>Pharmacy</span></div>
  <nav class="nav">
    <span>HOME</span><span>ABOUT US</span><span>SERVICES</span><span>PRODUCTS</span><span>NEWS</span><span>LINKS</span><span>CONTACTS</span>
    <svg width="10" height="10" viewBox="0 0 10 10"><circle cx="4" cy="4" r="3" fill="none" stroke="#4cc3da" stroke-width="1.4"/><line x1="6.3" y1="6.3" x2="9.2" y2="9.2" stroke="#4cc3da" stroke-width="1.4"/></svg>
  </nav>
</header>

<section class="hero" role="img" aria-label="Pharmacist's hands holding a medicine box and prescription paper">
  <span class="arrow prev"><svg width="8" height="8" viewBox="0 0 8 8"><path d="M5.5 1 2.5 4l3 3" fill="none" stroke="#fff" stroke-width="1.4"/></svg></span>
  <span class="arrow next"><svg width="8" height="8" viewBox="0 0 8 8"><path d="M2.5 1l3 3-3 3" fill="none" stroke="#fff" stroke-width="1.4"/></svg></span>
</section>

<section class="about">
  <h2>About Meadowbrook Pharmacy</h2>
  <p>Well suited to every patient, the practice of compounding has been trusted for generations. Our pharmacists prepare each medicine by hand in a purpose built laboratory, tailored to the exact dose, strength and form that your doctor or vet prescribes.</p>
  <p>This gives patients a real choice when standard products do not fit their needs. We work closely with medical and veterinary teams to create allergy free, flavoured and easy to take treatments for people and their animals.</p>
  <span class="more">Read More &gt;&gt;</span>
  <svg class="circles" width="230" height="210" viewBox="0 0 230 210" font-family="Open Sans, Arial, sans-serif" font-size="7.5" fill="#fff" text-anchor="middle">
    <circle cx="60" cy="60" r="54" fill="var(--circle-blue)" opacity=".92"/>
    <circle cx="160" cy="60" r="54" fill="var(--circle-green)" opacity=".92"/>
    <circle cx="110" cy="150" r="54" fill="var(--circle-teal)" opacity=".92"/>
    <path d="M50 42c-5-7-14-2-10 6l10 9 10-9c4-8-5-13-10-6z" fill="#fff"/>
    <text x="50" y="74">Personal</text><text x="50" y="83">Care</text>
    <path d="M165 38h8M167 38v8l-5 10h14l-5-10v-8" fill="none" stroke="#fff" stroke-width="2"/>
    <text x="170" y="72">What is</text><text x="170" y="81">Compounding</text>
    <polygon points="110,128 113.5,136 122,136.5 115.5,142 117.5,150 110,145.5 102.5,150 104.5,142 98,136.5 106.5,136" fill="#fff"/>
    <text x="110" y="164">Be</text><text x="110" y="173">Rewarded</text>
  </svg>
</section>

<section class="featured">
  <h2>Featured Products</h2>
  <div class="products">
    <div class="product"><div class="shot" role="img" aria-label="Jar of chest rub ointment" style="background:linear-gradient(160deg,#e9f1fa,#2f6fbf 45%,#1f5aa8 70%,#e9f1fa)"></div></div>
    <div class="product"><div class="shot" role="img" aria-label="Bottle of vitamin tablets with loose tablets" style="background:linear-gradient(160deg,#f7efe2,#c98d3f 45%,#e8d2a8 75%,#fbf7ef)"></div></div>
    <div class="product"><div class="shot" role="img" aria-label="Cold and flu medicine packs" style="background:linear-gradient(160deg,#2d4f9e,#5b77bf 40%,#e9a42b 70%,#f4d27a)"></div></div>
    <div class="product"><div class="shot" role="img" aria-label="Immune support supplement boxes" style="background:linear-gradient(160deg,#fbf6e2,#f0c93a 40%,#e65a3a 75%,#fbf2ea)"></div></div>
  </div>
  <div class="pager">
    <span><svg width="7" height="7" viewBox="0 0 8 8"><path d="M5.5 1 2.5 4l3 3" fill="none" stroke="#fff" stroke-width="1.5"/></svg></span>
    <span><svg width="7" height="7" viewBox="0 0 8 8"><path d="M2.5 1l3 3-3 3" fill="none" stroke="#fff" stroke-width="1.5"/></svg></span>
  </div>
</section>

<section class="callband">
  <svg class="icon" viewBox="0 0 24 24"><path d="M6.6 10.8c1.4 2.8 3.8 5.1 6.6 6.6l2.2-2.2c.3-.3.7-.4 1-.2 1.1.4 2.3.6 3.6.6.6 0 1 .4 1 1V20c0 .6-.4 1-1 1C10.6 21 3 13.4 3 4c0-.6.4-1 1-1h3.5c.6 0 1 .4 1 1 0 1.3.2 2.5.6 3.6.1.3 0 .7-.2 1z" fill="#fff"/></svg>
  <div class="label">Call Us Now</div>
  <div class="number">1 800 555 0142</div>
</section>

<section class="map" role="img" aria-label="Road map showing the pharmacy's location"></section>

<footer class="footer">
  <div>
    <div class="links"><span>Home</span><span>About Us</span><span>Services</span><span>Products</span><span>News</span><span>Links</span><span>Contacts</span></div>
    <div class="copy">Copyright © Meadowbrook Pharmacy 2024. All rights reserved.</div>
  </div>
  <div class="social" aria-label="Social links"><span></span><span></span><span></span><span></span><span></span></div>
</footer>
</body>
</html>
```